Letter design, envelope design, and more

Hello, we the Tavrin Gmbh are looking for our shop. Letter C5. Design does not have to be like a business card, so it can have straight lines. Only the color is important. The logo is the text under TaVRin omit.It should not be playful but Profesionel

Font styles to use
Sans Serif

Colors
0555a3
3176b5
85abd2
85cae6
34a7d8
0792cd
cee9f5
cfdfed
000000

Requirements
Must have
• Color like business card, Please, with the text under TaVRin, Correct address Lindmattstr. 4 Zip code 9517 Feldwil, as well as Couvert Without addressing only design and logo with TaVrn
Nice to have
• more writing articles
Should not have
• Not too colored, Text under TaVRin, bright colors

```html
<!DOCTYPE html>
<html lang="en">
<head>
<meta charset="utf-8">
<title>Tavrin Gmbh – Stationery</title>
<link href="https://fonts.googleapis.com/css2?family=Lato:wght@400;700&family=Yellowtail&display=swap" rel="stylesheet">
<style>
  :root{
    --stage:#e1e2e4;
    --paper:#ffffff;
    --navy:#23226a;
    --slate:#7b93ab;
    --stripe:#5a74a3;
    --text:#3c3c4a;
    --edge:#c9ccd2;
  }
  *{margin:0;padding:0;box-sizing:border-box}
  html,body{width:1200px;height:657px;overflow:hidden;background:var(--stage)}
  body{position:relative;font-family:'Lato',sans-serif;color:var(--text)}

  .sheet{position:absolute;background:var(--paper);border:1px solid var(--edge);overflow:hidden}

  /* Letterhead */
  .letterhead{left:48px;top:62px;width:379px;height:534px}
  .brand{display:flex;align-items:center;gap:6px;color:var(--navy);font-weight:700;letter-spacing:1px;white-space:nowrap}
  .brand-mark{width:14px;height:14px;background:var(--navy);flex:none}
  .letterhead .brand{position:absolute;left:21px;top:22px;font-size:19px}
  .contact{position:absolute;left:272px;top:10px;padding-left:7px;border-left:1px solid #b8bccb;font-size:7.4px;line-height:9px;color:#2c2c3c;font-style:normal}
  .contact-row{display:flex;gap:3px;align-items:flex-start;white-space:nowrap}
  .contact-row + .contact-row{margin-top:6px}
  .contact-row.tight{margin-top:2px}
  .contact svg{width:7px;height:7px;flex:none;margin-top:1px}
  .salutation{position:absolute;left:21px;top:88px;font-size:9.6px;font-weight:700;color:var(--navy)}
  .body{position:absolute;left:21px;top:108px;width:340px;font-size:6.9px;line-height:11.6px;text-align:justify;color:#45455a}
  .body p + p{margin-top:9px}
  .closing{position:absolute;left:21px;top:411px;font-size:11.5px;color:#3a3a48}
  .signature{position:absolute;left:21px;top:428px;font-family:'Yellowtail',cursive;font-size:21px;line-height:26px;color:var(--navy)}
  .footer-band{position:absolute;left:0;bottom:0;width:100%}
  .footer-web{position:absolute;right:24px;color:#fff;font-size:9.6px;letter-spacing:2.2px}
  .letterhead .footer-web{bottom:5px}

  /* Envelopes */
  .env-back{left:589px;top:100px;width:563px;height:252px}
  .env-back svg{position:absolute;left:0;top:0}
  .env-back .brand{position:absolute;left:0;width:100%;top:26px;justify-content:center;color:#fff;font-size:20px}
  .env-back .brand-mark{background:#fff}
  .env-mid{left:548px;top:208px;width:563px;height:251px}
  .env-mid svg{position:absolute;left:0;top:0}
  .env-mid .brand{position:absolute;left:0;width:100%;top:30px;justify-content:center;font-size:20px}
  .env-front{left:454px;top:320px;width:563px;height:252px}
  .env-front .brand{position:absolute;left:23px;top:30px;font-size:22px}
  .return-address{position:absolute;left:22px;top:66px;display:flex;gap:4px;align-items:center;font-size:9.6px;color:#1f1f2e;white-space:nowrap}
  .return-address svg{width:8px;height:8px}
  .env-front .footer-web{bottom:4px}
</style>
</head>
<body>

<!-- Letterhead -->
<section class="sheet letterhead">
  <div class="brand"><span class="brand-mark"></span>TAVRIN GMBH</div>

  <address class="contact">
    <div class="contact-row">
      <svg viewBox="0 0 10 10"><circle cx="5" cy="4" r="3.3" fill="none" stroke="#23226a" stroke-width="1.2"/><circle cx="5" cy="4" r="1.1" fill="#23226a"/><path d="M3 6.5 5 9.5 7 6.5" fill="#23226a"/></svg>
      <span>Lindmattstr. 4<br>Zip code 9517 Feldwil</span>
    </div>
    <div class="contact-row">
      <svg viewBox="0 0 10 10"><circle cx="5" cy="5" r="4.2" fill="none" stroke="#23226a" stroke-width="1"/><path d="M3.4 2.8 4.4 2.6 5 4 4.4 4.6Q5 5.8 5.6 6.2L6.2 5.6 7.4 6.2 7.2 7.2Q4.6 7.4 3.4 2.8Z" fill="#23226a"/></svg>
      <span>+41 71 555 02 47</span>
    </div>
    <div class="contact-row tight">
      <svg viewBox="0 0 10 10"><rect x="0.5" y="2" width="9" height="6" fill="#23226a"/><path d="M0.5 2 5 5.5 9.5 2" fill="none" stroke="#fff" stroke-width="0.8"/></svg>
      <span>info@tavrin.ch</span>
    </div>
  </address>

  <h2 class="salutation">Dear Mr. Lorem,</h2>

  <div class="body">
    <p>Lorem ipsum dolor sit amet, consectetuer adipiscing elit, sed diam nonummy nibh euismod tincidunt ut laoreet dolore magna aliquam erat volutpat. Ut wisi enim ad minim veniam, quis nostrud exerci tation ullamcorper suscipit lobortis nisl ut aliquip ex ea commodo consequat. Duis autem vel eum iriure dolor in hendiusto odio dignissim qui blandit praesent luptatum zzril delenit facilisi.</p>
    <p>Lorem ipsum dolor sit amet, consectetuer adipiscing elit, sed diam nonummy nibh euismod tincidunt ut laoreet dolore magna aliquam erat volutpat. Ut wisi enim ad minim veniam, quis nostrud exerci tation ullamcorper suscipit lobortis nisl ut aliquip ex ea commodo consequat.</p>
    <p>Lorem ipsum dolor sit amet, consectetuer adipiscing elit, sed diam nonummy nibh euismod tincidunt ut laoreet dolore magna aliquam erat volutpat. Ut wisi enim ad minim veniam, quis nostrud exerci tation ullamcorper suscipit lobortis nisl ut aliquip ex ea commodo consequat. Duis autem vel eum iriure dolor in hendiusto odio dignissim qui blandit praesent luptatum zzril delenit facilisi.</p>
    <p>Lorem ipsum dolor sit amet, consectetuer adipiscing elit, sed diam nonummy nibh euismod tincidunt ut laoreet dolore magna aliquam erat volutpat. Ut wisi enim ad minim veniam, quis nostrud exerci tation ullamcorper suscipit lobortis nisl ut aliquip ex ea commodo consequat.</p>
    <p>Lorem ipsum dolor sit amet, consectetuer adipiscing elit, sed diam nonummy nibh euismod tincidunt ut laoreet dolore magna aliquam erat volutpat. Ut wisi enim ad minim veniam, quis nostrud exerci tation ullamcorper suscipit lobortis nisl ut aliquip ex ea commodo consequat. Duis autem vel eum iriure dolor in hendiusto odio dignissim qui blandit praesent luptatum zzril delenit facilisi.</p>
    <p>Lorem ipsum dolor sit amet, consectetuer adipiscing elit, sed diam nonummy nibh euismod tincidunt ut laoreet dolore magna aliquam erat volutpat. Ut wisi enim ad minim veniam, quis nostrud exerci tation ullamcorper suscipit lobortis nisl ut aliquip ex ea commodo consequat.</p>
  </div>

  <p class="closing">Sincerely Your,</p>
  <p class="signature">Your Name</p>

  <svg class="footer-band" width="379" height="21" viewBox="0 0 379 21">
    <path d="M0 2H300C288 2 286 7 270 7H0Z" fill="var(--stripe)"/>
    <path d="M0 7H270C284 7 286 0 300 0H379V21H0Z" fill="var(--navy)"/>
  </svg>
  <span class="footer-web">www.tavrin.ch</span>
</section>

<!-- Envelope, back with coloured flap -->
<section class="sheet env-back">
  <svg width="563" height="252" viewBox="0 0 563 252">
    <path d="M0 0H563L556 34Q552 50 530 56L300 117Q283 121 266 117L36 56Q14 50 8 34Z" fill="var(--slate)"/>
  </svg>
  <div class="brand"><span class="brand-mark"></span>TAVRIN</div>
</section>

<!-- Envelope, back with outlined flap -->
<section class="sheet env-mid">
  <svg width="563" height="251" viewBox="0 0 563 251">
    <path d="M0 0 8 30Q14 44 36 50L266 95Q283 99 300 95L530 50Q552 44 556 30L563 0" fill="none" stroke="#bfc2c8" stroke-width="1"/>
  </svg>
  <div class="brand"><span class="brand-mark"></span>TAVRIN</div>
</section>

<!-- Envelope, front -->
<section class="sheet env-front">
  <div class="brand"><span class="brand-mark"></span>TAVRIN GMBH</div>
  <p class="return-address">
    <svg viewBox="0 0 10 10"><circle cx="5" cy="4" r="3.3" fill="none" stroke="#23226a" stroke-width="1.2"/><circle cx="5" cy="4" r="1.1" fill="#23226a"/><path d="M3 6.5 5 9.5 7 6.5" fill="#23226a"/></svg>
    Lindmattstr. 4, Zip code 9517 Feldwil
  </p>
  <svg class="footer-band" width="563" height="20" viewBox="0 0 563 20">
    <path d="M0 6H430C418 6 416 11 400 11H0Z" fill="var(--stripe)"/>
    <path d="M0 11H400C414 11 416 0 432 0H563V20H0Z" fill="var(--navy)"/>
  </svg>
  <span class="footer-web">www.tavrin.ch</span>
</section>

</body>
</html>
```